Heritage Hollow Business Cards

Require a business card design. <br/><br/>Needs to include logo (either round or long version) plus these details:<br/>Maya Torvell<br/>Heritage Hollow<br/>maya@kelvadtrading.com.au<br/>02 6481 7395<br/>PO Box Glenwarra NSW 2791<br/>www.heritagehollow.com.au<br/><br/>I need in an editable format so that I can create for multiple staff members. <br/><br/>

Target Market(s)

We are an online store selling renovation products to home owners are builders. Looking for a classic classy design.

Industry/Entity Type

Home And Garden

Contact Information for Business Card

Maya Torvell
Heritage Hollow
maya@kelvadtrading.com.au
02 6481 7395
PO Box Glenwarra NSW 2791
www.heritagehollow.com.au

Colors

Designer to choose colors to be used in the design.

Requirements
Must have
• Must include Logo.

```html
<!DOCTYPE html>
<html lang="en">
<head>
<meta charset="utf-8">
<title>Heritage Hollow Business Cards</title>
<link rel="stylesheet" href="https://fonts.googleapis.com/css2?family=Open+Sans:wght@400;600&family=Tinos:wght@700&display=swap">
<style>
  :root {
    --backdrop: #262626;
    --card: #050505;
    --silver: #d6d6d6;
    --text: #e4e4e4;
    --accent: #6d8a7a;
    --rule: #bdbdbd;
  }
  * { box-sizing: border-box; margin: 0; padding: 0; }
  html, body {
    width: 1200px; height: 960px; overflow: hidden;
    background: var(--backdrop);
  }
  .sheet {
    width: 1200px; height: 960px;
    display: flex; flex-direction: column; align-items: center; justify-content: center;
    gap: 48px;
  }
  .card {
    position: relative;
    width: 720px; height: 411px;
    background: var(--card);
    border-radius: 4px;
    box-shadow: 0 12px 30px rgba(0,0,0,.45);
    overflow: hidden;
  }
  .wordmark {
    font-family: "Open Sans", sans-serif;
    font-weight: 600;
    color: var(--silver);
    letter-spacing: .5px;
  }
  /* front */
  .card--front { display: flex; align-items: center; justify-content: center; gap: 22px; }
  .card--front .wordmark { font-size: 56px; }
  .mark-circle {
    width: 58px; height: 58px; border-radius: 50%;
    border: 2px solid var(--rule);
    flex: none;
  }
  /* back */
  .contact {
    position: absolute; left: 44px; top: 52px;
    font-family: "Open Sans", sans-serif;
    color: var(--text);
  }
  .contact__head { border-left: 8px solid var(--accent); padding-left: 14px; margin-bottom: 22px; }
  .contact__name { font-family: "Tinos", serif; font-weight: 700; font-size: 22px; line-height: 1.1; }
  .contact__role { font-family: "Tinos", serif; font-weight: 700; font-size: 15px; }
  .contact__address { font-size: 16px; line-height: 1.35; margin: 0 0 18px 22px; }
  .contact__list { list-style: none; font-size: 16px; line-height: 1.8; }
  .contact__list li { display: flex; align-items: center; gap: 10px; }
  .contact__list svg { width: 14px; height: 14px; flex: none; }
  .logo-round {
    position: absolute; right: 48px; top: 70px;
    width: 270px; height: 270px; border-radius: 50%;
    border: 2px solid var(--rule);
    display: flex; align-items: center; justify-content: center;
    text-align: center;
  }
  .logo-round .wordmark { font-size: 38px; line-height: 1.1; }
</style>
</head>
<body>
<main class="sheet">
  <section class="card card--front" aria-label="Card front">
    <span class="mark-circle" aria-hidden="true"></span>
    <span class="wordmark">Heritage Hollow</span>
  </section>

  <section class="card card--back" aria-label="Card back">
    <div class="contact">
      <div class="contact__head">
        <p class="contact__name">Maya Torvell</p>
        <p class="contact__role">Director</p>
      </div>
      <p class="contact__address">PO Box Glenwarra<br>NSW 2791</p>
      <ul class="contact__list">
        <li>
          <svg viewBox="0 0 16 16" aria-hidden="true"><path fill="var(--accent)" d="M3.6 1.2 6 3.6 4.7 5.6c.8 1.9 2.1 3.2 4 4l1.9-1.3 2.4 2.4-1.4 2.3C6.3 13 1.9 8.5 1.3 2.6z"/></svg>
          <span>02 6481 7395</span>
        </li>
        <li>
          <svg viewBox="0 0 16 16" aria-hidden="true"><rect x="1" y="3" width="14" height="10" fill="var(--accent)"/><path d="M1 3l7 6 7-6" fill="none" stroke="var(--card)" stroke-width="1.3"/></svg>
          <span>maya@kelvadtrading.com.au</span>
        </li>
        <li>
          <svg viewBox="0 0 16 16" aria-hidden="true"><g fill="none" stroke="var(--accent)" stroke-width="1.3"><circle cx="8" cy="8" r="6.5"/><ellipse cx="8" cy="8" rx="2.8" ry="6.5"/><path d="M1.5 8h13"/></g></svg>
          <span>www.heritagehollow.com.au</span>
        </li>
      </ul>
    </div>
    <div class="logo-round">
      <span class="wordmark">Heritage<br>Hollow</span>
    </div>
  </section>
</main>
</body>
</html>
```